Brell Stone Company Business Cards

Front and Back Business Card - logo and text setup - cool design. I need workable photoshop or illustrator files so I can setup each employee card with design that is created
Updates

Hi everyone, thank you for the great entries. Please no more white and blue cards - there are so many already - black and silver only now please. thanks!

Target Market(s)

Construction Industry - Facility Managers

Industry/Entity Type

Construction

Contact Information for Business Card

I really like contemporary simplistic looks - clean neat....not opposed to seeing some black backrounds

Requirements
Must have
• Logo/website address with design on front only - www.brellstone-example.com (logo attached)
• Back:
• Name/Title/Company Address/Phone/email address
Nice to have
• Cool design
Should not have
• Nothing gimmicky like Fire or Water - since we are a Fire Protection company - it has all been done

```html
<!DOCTYPE html>
<html lang="en">
<head>
<meta charset="utf-8">
<title>Brell Stone Company Business Cards</title>
<link href="https://fonts.googleapis.com/css2?family=Open+Sans:wght@400;600;700;800&display=swap" rel="stylesheet">
<style>
  :root {
    --backdrop: #6e7073;
    --card-black: #121314;
    --panel-black: #1c1d1f;
    --panel-black-deep: #0b0b0c;
    --silver: #c9ccd0;
    --silver-light: #e4e6e9;
    --silver-dark: #8f9398;
    --ink-dark: #151617;
  }
  * { box-sizing: border-box; margin: 0; padding: 0; }
  html, body {
    width: 1200px; height: 1000px; overflow: hidden;
    background: var(--backdrop);
    font-family: "Open Sans", sans-serif;
  }
  .canvas { position: relative; width: 1200px; height: 1000px; }
  .card {
    position: absolute; left: 250px; width: 700px; height: 400px;
    overflow: hidden;
    box-shadow: 0 14px 30px rgba(0,0,0,0.35);
  }
  .card--logo { top: 70px; background: var(--card-black); }
  .card--contact { top: 530px; background: linear-gradient(150deg, var(--silver-light), var(--silver)); }

  .company-name {
    font-family: "Open Sans", sans-serif;
    font-weight: 800; letter-spacing: -0.5px; line-height: 1;
  }
  .card--logo .company-name {
    position: absolute; left: 0; right: 0; top: 135px;
    text-align: center; font-size: 50px; color: var(--silver);
  }
  .web-band {
    position: absolute; left: 300px; right: 0; top: 248px; height: 30px;
    background: linear-gradient(90deg, var(--silver-dark), var(--silver-light));
    display: flex; align-items: center; padding-left: 40px;
    color: var(--ink-dark); font-size: 15px; letter-spacing: 4px; font-weight: 600;
  }

  .card--contact .brand-side {
    position: absolute; left: 0; top: 0; width: 385px; height: 400px;
    display: flex; align-items: center; justify-content: center;
  }
  .card--contact .company-name { font-size: 34px; text-align: center; color: var(--ink-dark); }
  .divider {
    position: absolute; left: 388px; top: 0; width: 14px; height: 400px;
  }
  .info-panel {
    position: absolute; left: 402px; top: 0; right: 0; height: 400px;
    background: linear-gradient(160deg, var(--panel-black), var(--panel-black-deep));
    color: var(--silver-light); padding: 52px 0 0 34px;
  }
  .person-name { font-weight: 700; font-size: 19px; letter-spacing: 0.5px; color: #ffffff; }
  .person-title { font-weight: 400; font-size: 14px; letter-spacing: 0.5px; margin-top: 1px; color: var(--silver); }
  .address { margin-top: 118px; font-size: 15px; line-height: 1.35; }
  .contact-list { list-style: none; font-size: 15px; line-height: 1.35; margin-top: 2px; }
  .contact-list li { display: flex; align-items: center; gap: 10px; }
  .contact-list svg { width: 14px; height: 14px; flex: none; }
</style>
</head>
<body>
<main class="canvas">

  <section class="card card--logo" aria-label="Card front">
    <p class="company-name">Brell Stone Company</p>
    <div class="web-band">brellstone-example.com</div>
  </section>

  <section class="card card--contact" aria-label="Card back">
    <div class="brand-side">
      <p class="company-name">Brell Stone<br>Company</p>
    </div>
    <svg class="divider" viewBox="0 0 14 400" aria-hidden="true">
      <rect x="0" y="0" width="14" height="18" fill="#121314"/>
      <rect x="0" y="28" width="14" height="18" fill="#1d1e20"/>
      <rect x="0" y="56" width="14" height="18" fill="#2a2b2e"/>
      <rect x="0" y="84" width="14" height="18" fill="#37393c"/>
      <rect x="0" y="112" width="14" height="18" fill="#44464a"/>
      <rect x="0" y="140" width="14" height="18" fill="#525458"/>
      <rect x="0" y="168" width="14" height="18" fill="#606266"/>
      <rect x="0" y="196" width="14" height="18" fill="#6d7074"/>
      <rect x="0" y="224" width="14" height="18" fill="#7a7d81"/>
      <rect x="0" y="252" width="14" height="18" fill="#878a8e"/>
      <rect x="0" y="280" width="14" height="18" fill="#94979b"/>
      <rect x="0" y="308" width="14" height="18" fill="#a1a4a8"/>
      <rect x="0" y="336" width="14" height="18" fill="#aeb1b5"/>
      <rect x="0" y="364" width="14" height="18" fill="#b9bcc0"/>
    </svg>
    <div class="info-panel">
      <p class="person-name">MARCUS HALE</p>
      <p class="person-title">PRESIDENT</p>
      <p class="address">48 Harbor Line Road<br>Northfield, NY 11900</p>
      <ul class="contact-list">
        <li>
          <svg viewBox="0 0 16 16" aria-hidden="true"><path fill="#c9ccd0" d="M2 5c0-2 2-3 6-3s6 1 6 3v1h-3V5H5v1H2zM4 7h8l2 7H2z"/></svg>
          (555) 214-3308
        </li>
        <li>
          <svg viewBox="0 0 16 16" aria-hidden="true"><path fill="#c9ccd0" d="M4 1h8v4H4zM1 6h14v6h-3v3H4v-3H1zm4 4v4h6v-4z"/></svg>
          (555) 214-3309
        </li>
        <li>
          <svg viewBox="0 0 16 16" aria-hidden="true"><path fill="#c9ccd0" d="M1 3h14v10H1zm1.5 1.2L8 8.5l5.5-4.3z"/></svg>
          info@brellstone-example.com
        </li>
        <li>
          <svg viewBox="0 0 16 16" aria-hidden="true"><circle cx="8" cy="8" r="7" fill="#c9ccd0"/><path fill="#1c1d1f" d="M5 4c2 0 3 1 2 3S4 8 4 10 3 8 3 7s1-3 2-3zm5 4c2 0 3 1 2 3s-2 2-3 1 0-4 1-4z"/></svg>
          www.brellstone-example.com
        </li>
      </ul>
    </div>
  </section>

</main>
</body>
</html>
```